Healthy lifestyle Influencer business card

I need your creativity to have a business card that I can leave in all the restaurants, hotels and spas I visit to inform them that I am an influencer specializing in the wellness sector and that I will write a review about them. You can use my instagram photos Lunavita27 or on my website www.piattileggeriorto.it. I would like my business card to impress with its creativity! thank you very much!

Contact Information for Business Card

siteweb, instagram, phone number

Font styles to use
Decorative
Script

Colors
0094D4
00A9DD
6FCCEA
C7EBF8
E9F6FB
59FF00
82FF00
B8FF75
E3FFCB
F4FFEA
FFC000
F8CF3A
FAE287
FDF2CF
FEFAEE
F0912C
F2A743
F7CA91
FBE8D2
FDF5EE
EE7325
F08F49
F5BC92
FAE3D3
FDF4ED
EB3D1F
EC4F4E
F09395
F8D3D4
FCEDEE
E54698
E96AAD
F1A4CE
F9D9EA
FCEFF6

Requirements
Nice to have
• creativity

```html
<!DOCTYPE html>
<html lang="it">
<head>
<meta charset="utf-8">
<title>Luna Vita Chef – Business Card</title>
<link rel="stylesheet" href="https://fonts.googleapis.com/css2?family=Montserrat:wght@400;500;700&display=swap">
<style>
  :root {
    --bg: #3b3b3b;
    --card-white: #ffffff;
    --ink: #4a4a4a;
    --ink-soft: #666666;
    --accent: #f0912c;
    --divider: #e4e4e4;
    --crust-dark: #3a2414;
    --crust-mid: #8a5526;
    --crust-light: #b97a3a;
    --on-photo: #ffffff;
  }
  * { box-sizing: border-box; margin: 0; padding: 0; }
  html, body {
    width: 1200px; height: 800px; overflow: hidden;
    background: var(--bg);
    font-family: "Montserrat", Arial, sans-serif;
  }
  .canvas {
    width: 1200px; height: 800px;
    display: flex; align-items: center; justify-content: center; gap: 40px;
  }
  .card {
    width: 540px; height: 309px;
    position: relative; overflow: hidden;
    box-shadow: 0 14px 30px rgba(0,0,0,0.35);
  }
  /* Front */
  .card-front { background: var(--card-white); display: flex; }
  .brand-side {
    width: 54%;
    display: flex; flex-direction: column; align-items: center; justify-content: center;
    border-right: 1px solid var(--divider);
  }
  .brand-name {
    display: flex; align-items: center; gap: 8px;
    font-weight: 500; font-size: 24px; color: var(--ink); letter-spacing: 0.5px;
  }
  .brand-dot { width: 10px; height: 10px; border-radius: 50%; background: var(--accent); opacity: 0.55; }
  .brand-tagline { margin-top: 8px; font-size: 10.5px; color: var(--ink-soft); letter-spacing: 0.4px; }
  .contact-side {
    width: 46%; padding: 0 22px;
    display: flex; flex-direction: column; justify-content: center;
  }
  .person-name { font-weight: 700; font-size: 17px; color: var(--ink); letter-spacing: 0.5px; }
  .person-role { font-size: 11px; color: var(--accent); margin-top: 2px; }
  .address { margin-top: 10px; font-size: 10.5px; color: var(--ink-soft); line-height: 1.5; }
  .contact-list { list-style: none; margin-top: 8px; }
  .contact-list li {
    display: flex; align-items: center; gap: 8px;
    font-size: 10.5px; color: var(--ink-soft); line-height: 1.75;
  }
  .contact-list svg { width: 11px; height: 11px; flex: none; }
  /* Back */
  .card-back { color: var(--on-photo); }
  .photo {
    position: absolute; inset: 0;
    background:
      linear-gradient(100deg, #5a5650 0%, var(--crust-dark) 14%, var(--crust-mid) 30%, var(--crust-dark) 44%, var(--crust-light) 58%, var(--crust-mid) 72%, var(--crust-dark) 90%, #2c1a0e 100%);
  }
  .back-logo {
    position: absolute; inset: 0;
    display: flex; flex-direction: column; align-items: center; justify-content: center;
  }
  .back-logo .brand-name { color: var(--on-photo); font-size: 30px; }
  .back-logo .brand-dot { background: var(--on-photo); opacity: 0.7; }
  .back-logo .brand-tagline { color: var(--on-photo); font-size: 13px; }
</style>
</head>
<body>
<main class="canvas">
  <section class="card card-front" aria-label="Fronte del biglietto">
    <div class="brand-side">
      <div class="brand-name"><span class="brand-dot"></span>Luna Vita Chef</div>
      <p class="brand-tagline">bene ogni giorno a tavola</p>
    </div>
    <div class="contact-side">
      <h1 class="person-name">GIULIA FERRI</h1>
      <p class="person-role">President</p>
      <p class="address">12 Via dei Tigli<br>Verona, Italia 37121</p>
      <ul class="contact-list">
        <li>
          <svg viewBox="0 0 12 12"><path d="M2.5 1h2l1 3-1.3 1a6 6 0 0 0 2.8 2.8L8 6.5l3 1v2a1.5 1.5 0 0 1-1.5 1.5A8.5 8.5 0 0 1 1 2.5 1.5 1.5 0 0 1 2.5 1z" fill="var(--accent)"/></svg>
          045.812.3367
        </li>
        <li>
          <svg viewBox="0 0 12 12"><rect x="1" y="2.5" width="10" height="7" rx="1" fill="var(--accent)"/><path d="M1.5 3l4.5 3.5L10.5 3" stroke="#fff" stroke-width="1" fill="none"/></svg>
          info@piattileggeriorto.it
        </li>
        <li>
          <svg viewBox="0 0 12 12"><circle cx="6" cy="6" r="5" fill="none" stroke="var(--accent)" stroke-width="1.2"/><path d="M1 6h10M6 1c-2 2.5-2 7.5 0 10M6 1c2 2.5 2 7.5 0 10" stroke="var(--accent)" stroke-width="0.9" fill="none"/></svg>
          www.piattileggeriorto.it
        </li>
        <li>
          <svg viewBox="0 0 12 12"><circle cx="6" cy="6" r="5" fill="var(--accent)"/></svg>
          @lunavita27
        </li>
      </ul>
    </div>
  </section>

  <section class="card card-back" aria-label="Retro del biglietto">
    <div class="photo" role="img" aria-label="Foto ravvicinata di un plumcake dorato appena sfornato"></div>
    <div class="back-logo">
      <div class="brand-name"><span class="brand-dot"></span>Luna Vita Chef</div>
      <p class="brand-tagline">bene ogni giorno a tavola</p>
    </div>
  </section>
</main>
</body>
</html>
```